Real Estate Text Messaging Info for house buyers and home sellers

We need a flyer (8 1/2 X 11) for a new service we are rolling out for my real estate business. It allows potential buyers to receive home information by texting "Doug" to 73816. This will instantly send the potential buyer the price, information and photos of the home they are sitting in front of. This works for not only Doug Fenwickley's listings,but for ANY and ALL homes currently listed in the MLS.
Here is a link that will give you more information. http://www.zopvin.example/index.aspx This is private labeled for Doug Fenwickley, Broker/Owner of Dalbrook Realtors - Summit Estates and should not have Zopvin anywhere in the flyer. I want the focus to be on receiving information instantly for buyers and for sellers it is an innovative way to promote their home. These should be two different types of flyers. I am looking for something that will grab potential buyers with the colors and the ease of use. Please include my website www.PineShoreHouseFacts.example and my phone number 218-555-HOME (4663).
Target Market(s)
home buyers and future home sellers
Industry/Entity Type
Real Estate
Look and feel

```html
<!DOCTYPE html>
<html lang="en">
<head>
<meta charset="utf-8">
<title>Text-for-Info Flyers – Doug Fenwickley</title>
<link rel="stylesheet" href="https://fonts.googleapis.com/css2?family=Dosis:wght@300;400;600;700&display=swap">
<style>
  :root {
    --page: #ffffff;
    --paper: #ffffff;
    --paper-fade: #eceef0;
    --ink: #1d1d1d;
    --ink-soft: #555;
    --ribbon: #fff21a;
    --ribbon-tail: #8a8a1e;
    --accent-blue: #1ba6e1;
    --accent-red: #e3171f;
  }
  * { box-sizing: border-box; margin: 0; padding: 0; }
  html, body { width: 1200px; height: 900px; overflow: hidden; background: var(--page); }
  body { font-family: "Dosis", "Arial Narrow", sans-serif; color: var(--ink); position: relative; }

  .flyer {
    position: absolute; top: 110px; width: 520px; height: 680px;
    background: linear-gradient(to bottom, var(--paper) 60%, var(--paper-fade));
    box-shadow: 0 6px 18px rgba(0,0,0,.25); overflow: hidden;
  }
  .flyer--buyer { left: 45px; }
  .flyer--seller { left: 635px; }

  .hero { position: absolute; left: 0; top: 0; width: 520px; height: 310px; }

  .ribbon {
    position: absolute; left: 50%; transform: translateX(-50%);
    background: var(--ribbon); color: var(--ink);
    font-weight: 400; text-transform: uppercase; white-space: nowrap;
    padding: 4px 16px; box-shadow: 0 2px 3px rgba(0,0,0,.3); z-index: 2;
  }
  .ribbon::before, .ribbon::after {
    content: ""; position: absolute; top: 8px; width: 34px; height: 100%;
    background: var(--ribbon-tail); z-index: -1;
  }
  .ribbon::before { left: -26px; clip-path: polygon(0 0,100% 0,100% 100%,0 100%,30% 50%); }
  .ribbon::after { right: -26px; clip-path: polygon(0 0,100% 0,70% 50%,100% 100%,0 100%); }
  .ribbon--headline { top: 30px; font-size: 24px; }
  .ribbon--promise { top: 215px; font-size: 21px; }
  .ribbon--callout {
    left: 22px; transform: none; top: 520px; font-size: 16px; padding: 2px 12px;
  }
  .ribbon--callout::before { display: none; }
  .underline { text-decoration: underline; }
  .dotted-box { border: 1px dashed var(--ink); padding: 0 2px; }

  .steps { position: absolute; top: 292px; left: 0; width: 520px; }
  .badge { position: absolute; top: 0; width: 116px; height: 116px; }
  .badge--1 { left: 30px; } .badge--2 { left: 202px; } .badge--3 { left: 374px; }
  .arrow { position: absolute; top: 48px; width: 40px; height: 20px; }
  .arrow--1 { left: 152px; } .arrow--2 { left: 324px; }

  .step-text {
    position: absolute; top: 124px; width: 146px; text-align: center;
    font-weight: 600; font-size: 13.5px; line-height: 1.35;
  }
  .step-text--1 { left: 15px; } .step-text--2 { left: 187px; } .step-text--3 { left: 359px; }
  .hl { color: var(--accent-blue); }
  .keyword { color: var(--accent-red); font-weight: 700; font-size: 20px; line-height: 1; }

  .divider { position: absolute; left: 60px; top: 546px; width: 230px; border-top: 2px dashed var(--accent-blue); }

  .contact { position: absolute; left: 10px; width: 282px; text-align: right; }
  .contact--buyer { top: 558px; }
  .contact--seller { top: 554px; }
  .contact__name { font-weight: 300; font-size: 27px; letter-spacing: 1px; line-height: 1.2; }
  .contact__title { font-size: 8.5px; color: var(--ink-soft); margin-bottom: 8px; white-space: nowrap; }
  .contact__line { font-size: 14px; font-weight: 400; margin-top: 4px; white-space: nowrap; }
  .contact__label { color: var(--accent-blue); margin-right: 4px; }

  .portrait {
    position: absolute; left: 298px; top: 514px; width: 84px; height: 166px;
    background: linear-gradient(to bottom, #f4f4f4, #d9dde2); border-radius: 42px 42px 0 0;
  }
  .brand {
    position: absolute; left: 390px; top: 592px; width: 116px; height: 70px;
    background: var(--paper); border-radius: 4px;
    display: flex; flex-direction: column; justify-content: center; align-items: center;
    font-weight: 700; font-size: 14px; line-height: 1.15; text-align: center; color: var(--ink);
  }
</style>
</head>
<body>
  <svg width="0" height="0" style="position:absolute">
    <defs>
      <linearGradient id="scene" x1="0" y1="0" x2="0" y2="1">
        <stop offset="0" stop-color="#9fc3e3"/>
        <stop offset=".35" stop-color="#dde9f2"/>
        <stop offset=".45" stop-color="#b59a7b"/>
        <stop offset=".75" stop-color="#a8906f"/>
        <stop offset=".85" stop-color="#8d9a55"/>
        <stop offset="1" stop-color="#7f8f45"/>
      </linearGradient>
      <symbol id="burst" viewBox="0 0 100 100">
        <polygon points="100,50 89.6,60.6 93.3,75 79,79 75,93.3 60.6,89.6 50,100 39.4,89.6 25,93.3 21,79 6.7,75 10.4,60.6 0,50 10.4,39.4 6.7,25 21,21 25,6.7 39.4,10.4 50,0 60.6,10.4 75,6.7 79,21 93.3,25 89.6,39.4" fill="#1ba6e1" stroke="#fff" stroke-width="2"/>
      </symbol>
      <symbol id="red-arrow" viewBox="0 0 40 20">
        <polygon points="0,7 26,7 26,1 40,10 26,19 26,13 0,13" fill="#e3171f"/>
      </symbol>
    </defs>
  </svg>

  <article class="flyer flyer--buyer">
    <svg class="hero" viewBox="0 0 520 310" role="img" aria-label="Photo of a two-storey stucco and stone house with double garage, lawn and blue sky">
      <path d="M0 0H520V110C470 230 330 255 200 262C110 267 40 285 0 300Z" fill="url(#scene)"/>
    </svg>
    <div class="ribbon ribbon--headline">Found your dream house?</div>
    <div class="ribbon ribbon--promise">Get details on the spot, instantly!</div>

    <div class="steps">
      <svg class="badge badge--1" viewBox="0 0 100 100" aria-hidden="true">
        <use href="#burst"/>
        <rect x="30" y="22" width="40" height="58" rx="6" fill="#222" transform="rotate(-12 50 50)"/>
        <rect x="34" y="28" width="32" height="44" fill="#fff" transform="rotate(-12 50 50)"/>
        <text x="50" y="55" text-anchor="middle" font-family="Dosis, sans-serif" font-weight="700" font-size="12" fill="#e3171f" transform="rotate(-12 50 50)">DOUG</text>
      </svg>
      <svg class="arrow arrow--1" viewBox="0 0 40 20" aria-hidden="true"><use href="#red-arrow"/></svg>
      <svg class="badge badge--2" viewBox="0 0 100 100" aria-hidden="true">
        <use href="#burst"/>
        <path d="M50 40L36 82M50 40L64 82M40 70H60M43 58H57" stroke="#fff" stroke-width="4" fill="none"/>
        <circle cx="50" cy="36" r="6" fill="#e3171f"/>
        <path d="M50 20V26M38 26L42 30M62 26L58 30M34 36H40M60 36H66" stroke="#e3171f" stroke-width="2"/>
      </svg>
      <svg class="arrow arrow--2" viewBox="0 0 40 20" aria-hidden="true"><use href="#red-arrow"/></svg>
      <svg class="badge badge--3" viewBox="0 0 100 100" aria-hidden="true">
        <use href="#burst"/>
        <rect x="34" y="22" width="30" height="38" fill="#eee" stroke="#999"/>
        <rect x="28" y="30" width="38" height="48" fill="#fff" stroke="#999"/>
        <path d="M33 40H60M33 47H60M33 54H60M33 61H55" stroke="#aaa" stroke-width="2"/>
        <path d="M52 66L60 74L78 52" stroke="#8bc34a" stroke-width="5" fill="none"/>
      </svg>

      <p class="step-text step-text--1">Text the word<br><span class="keyword">“DOUG”</span><br>to <span class="keyword">73816</span><br>while infront of the house you’re interested in.</p>
      <p class="step-text step-text--2">Our server identifies where you are using your GPS position and sends out <span class="hl">all the information you need</span>.</p>
      <p class="step-text step-text--3">You <span class="hl">instantly</span> receive, photos, details and a price for <span class="hl">your dream home!</span></p>
    </div>

    <div class="divider"></div>
    <div class="contact contact--buyer">
      <p class="contact__name">Doug Fenwickley</p>
      <p class="contact__title">Broker/Owner of Dalbrook Realtors - Summit Estates</p>
      <p class="contact__line"><span class="contact__label">visit:</span>www.PineShoreHouseFacts.example</p>
      <p class="contact__line"><span class="contact__label">call:</span>218-555-HOME (4663)</p>
    </div>
    <div class="portrait" role="img" aria-label="Portrait of the broker in shirt and tie"></div>
    <div class="brand"><span>Dalbrook Realtors</span><span>Summit Estates</span></div>
  </article>

  <article class="flyer flyer--seller">
    <svg class="hero" viewBox="0 0 520 310" role="img" aria-label="Photo of a two-storey stucco and stone house with double garage, lawn and blue sky">
      <path d="M0 0H520V110C470 230 330 255 200 262C110 267 40 285 0 300Z" fill="url(#scene)"/>
    </svg>
    <div class="ribbon ribbon--headline">Selling your home?</div>
    <div class="ribbon ribbon--promise">Make it <span class="dotted-box">instantly</span> accessable to buyers!</div>

    <div class="steps">
      <svg class="badge badge--1" viewBox="0 0 100 100" aria-hidden="true">
        <use href="#burst"/>
        <rect x="30" y="22" width="40" height="58" rx="6" fill="#222" transform="rotate(-12 50 50)"/>
        <rect x="34" y="28" width="32" height="44" fill="#fff" transform="rotate(-12 50 50)"/>
        <text x="50" y="55" text-anchor="middle" font-family="Dosis, sans-serif" font-weight="700" font-size="12" fill="#e3171f" transform="rotate(-12 50 50)">DOUG</text>
      </svg>
      <svg class="arrow arrow--1" viewBox="0 0 40 20" aria-hidden="true"><use href="#red-arrow"/></svg>
      <svg class="badge badge--2" viewBox="0 0 100 100" aria-hidden="true">
        <use href="#burst"/>
        <path d="M50 40L36 82M50 40L64 82M40 70H60M43 58H57" stroke="#fff" stroke-width="4" fill="none"/>
        <circle cx="50" cy="36" r="6" fill="#e3171f"/>
        <path d="M50 20V26M38 26L42 30M62 26L58 30M34 36H40M60 36H66" stroke="#e3171f" stroke-width="2"/>
      </svg>
      <svg class="arrow arrow--2" viewBox="0 0 40 20" aria-hidden="true"><use href="#red-arrow"/></svg>
      <svg class="badge badge--3" viewBox="0 0 100 100" aria-hidden="true">
        <use href="#burst"/>
        <rect x="34" y="22" width="30" height="38" fill="#eee" stroke="#999"/>
        <rect x="28" y="30" width="38" height="48" fill="#fff" stroke="#999"/>
        <path d="M33 40H60M33 47H60M33 54H60M33 61H55" stroke="#aaa" stroke-width="2"/>
        <path d="M52 66L60 74L78 52" stroke="#8bc34a" stroke-width="5" fill="none"/>
      </svg>

      <p class="step-text step-text--1">A potential buyer texts the word <span class="keyword">“DOUG”</span><br>to <span class="keyword">73816</span><br>while infront of your house.</p>
      <p class="step-text step-text--2">Our server pinpoints their GPS position and sends out <span class="hl">all the information they need</span>.</p>
      <p class="step-text step-text--3">They <span class="hl">instantly</span> receive the price, details and photos of <span class="hl">your home!</span></p>
    </div>

    <div class="ribbon ribbon--callout">Ask about this service <span class="underline">now</span>!</div>
    <div class="contact contact--seller">
      <p class="contact__name">Doug Fenwickley</p>
      <p class="contact__title">Broker/Owner of Dalbrook Realtors - Summit Estates</p>
      <p class="contact__line"><span class="contact__label">visit:</span>www.PineShoreHouseFacts.example</p>
      <p class="contact__line"><span class="contact__label">call:</span>218-555-HOME (4663)</p>
    </div>
    <div class="portrait" role="img" aria-label="Portrait of the broker in shirt and tie"></div>
    <div class="brand"><span>Dalbrook Realtors</span><span>Summit Estates</span></div>
  </article>
</body>
</html>
```